3 Business Card designs for a company with multiple services

We are a company that has 3 main services:

1) Security - CCTV & Alarm Sepcialists
2) Broadcast - Broadcast Sales and Technical Services
3) Distribution - Quality Products, Quality Service

The broadcast service is for Video Broadcast.

I will include our logos for each service.

I would like to also create a business card design for 7QR in general (see main logo).

Each card will be two-sided. On the front I would think it would include Logo, Name, Posistion and Mobile (and possibly email). And possibly our main number (which may be something like 1800 639 415)

On the back it MUST include a "lined" section to be able to write short quotes / prices.

Then include more details like Phone: 1800 639 415 Fax: 1800 639 417 Postal: PO Box 917, Tallowfield, QLD Australia 4287 Website: www.7qr.com.au

We would like a fresh, inovative card design with that "wow check this out" feel about it.

Look forward to seeing what you can do! :)

Corin

• Quote section on the back!
Editable files.

```html
<!DOCTYPE html>
<html lang="en">
<head>
<meta charset="utf-8">
<title>7QR Business Card – Back</title>
<link rel="stylesheet" href="https://fonts.googleapis.com/css2?family=Arimo:wght@400&display=swap">
<style>
  :root {
    --card-bg: #e6e6e6;
    --card-bg-light: #f2f2f2;
    --paper: #ececec;
    --rule-dark: #2a2a2a;
    --rule-blue: #1c2a7a;
    --label-blue: #1a2a85;
    --detail-grey: #6f6f6f;
    --brand-ink: #2b2b2b;
  }
  html, body {
    margin: 0;
    padding: 0;
    overflow: hidden;
  }
  .card {
    position: relative;
    width: 1200px;
    height: 721px;
    overflow: hidden;
    background: radial-gradient(ellipse at 55% 40%, var(--card-bg-light) 0%, var(--card-bg) 60%, #d6d6d6 100%);
    font-family: "Arimo", Arial, sans-serif;
  }
  .pattern-panel {
    position: absolute;
    right: 0;
    top: 0;
    width: 370px;
    height: 721px;
    background: linear-gradient(90deg, rgba(0,0,0,0) 0%, rgba(120,120,120,0.12) 40%, rgba(110,110,110,0.18) 100%);
  }
  .papers {
    position: absolute;
    left: 0;
    top: 0;
  }
  .quote-lines {
    position: absolute;
    left: 332px;
    top: 229px;
    width: 680px;
  }
  .quote-line {
    height: 0;
    border-top: 1.5px solid var(--rule-dark);
    margin-bottom: 45px;
  }
  .brand {
    position: absolute;
    right: 190px;
    top: 418px;
    height: 72px;
    display: flex;
    align-items: center;
    gap: 22px;
  }
  .brand-mark {
    width: 40px;
    height: 40px;
    background: var(--brand-ink);
  }
  .brand-name {
    font-size: 60px;
    line-height: 72px;
    color: var(--brand-ink);
    letter-spacing: 10px;
    margin-right: -10px;
  }
  .blue-rule {
    position: absolute;
    left: 448px;
    top: 514px;
    width: 564px;
    border-top: 2px solid var(--rule-blue);
  }
  .contact {
    position: absolute;
    right: 188px;
    top: 538px;
    text-align: right;
    font-size: 23.5px;
    line-height: 29px;
    color: var(--detail-grey);
    letter-spacing: 0.6px;
  }
  .contact .label {
    color: var(--label-blue);
  }
  .contact .website {
    padding-right: 7px;
  }
</style>
</head>
<body>
<div class="card">
  <div class="pattern-panel" role="img" aria-label="Faint repeating brand pattern fading in from the right edge"></div>

  <svg class="papers" width="1200" height="721" viewBox="0 0 1200 721" aria-hidden="true">
    <defs>
      <filter id="paper-shadow" x="-10%" y="-10%" width="130%" height="130%">
        <feDropShadow dx="2" dy="3" stdDeviation="4" flood-color="#000" flood-opacity="0.18"/>
      </filter>
    </defs>
    <polygon points="43,0 218,229 512,0" fill="var(--paper)" filter="url(#paper-shadow)"/>
    <polygon points="0,181 101,103 378,467 48,721 0,721" fill="var(--paper)" filter="url(#paper-shadow)"/>
  </svg>

  <div class="quote-lines">
    <div class="quote-line"></div>
    <div class="quote-line"></div>
    <div class="quote-line"></div>
    <div class="quote-line"></div>
  </div>

  <div class="brand">
    <span class="brand-mark"></span>
    <span class="brand-name">7QR</span>
  </div>

  <div class="blue-rule"></div>

  <div class="contact">
    <div><span class="label">Phone:</span> 1800 639 415 Fax: 1800 639 417</div>
    <div><span class="label">Postal:</span> PO Box 917, Tallowfield, QLD Australia 4287</div>
    <div class="website"><span class="label">Website:</span> www.7qr.com.au</div>
  </div>
</div>
</body>
</html>
```